July 2022 Industrial Manufacturer Product Expo Mexico City

We manufacture large screws and fastners for large Mining equipment, Trains, large ships, airplanes, wind turbines, and so on. We also do custom work base on the customer needs. No matter the size we can make it.
We have a Expo coming up with companies all over the world. We have to stand out we are a family own business so our customer service will be above and beyond anyone can provide. We do not have a sales force to push our products and services we provide one on one service.
Plus@!! I'm looking for anything that you designers can come up with if it was your company to put on a business card, plus i want to do a 1 or 2 sided pamphlet, and then a website. We make Speciality Bolts for large mining equipment these bolts can be 3 to 4 foot long!!! Plus fasteners, Nuts, washers, any, size, strengths, special materials, we offer more of a ono on one customer service, We are a small company, family own, but can fulfill any type of orders. We can also provide special time lines for emergency orders. "We keep the machines running we here at KRV don't believe in down time" We want to hear any slogan based on our company to stand out.
Thanks i really appreciate all your work and options that we have to pick on. Plus just a thought we could possibly want to entertain a experience Marketing internet help maybe a employment possibility. Thanks

I need 2 cards one in Spanish and English Like the steel back ground maybe send me in some bright red and blue writing Same with the Black cards Please remove the word Military The logo KRV maybe integrate a picture of a Bolt 🔩 Thank you

Still looking for I need 2 cards one in Spanish and English Like the steel back ground maybe send me in some bright red and blue writing Same with the Black cards try bright writing Please remove the word Military The logo KRV maybe integrate a picture of a Bolt 🔩 Plus will need the company to make a brochure and website next Thank you

Target Market(s)

Large Mining, Ship, Train, Green Energy, VELM, and Government equipment. Throughout the World

Industry/Entity Type

We can Custom Manufacture any type of Fastners for Mining equipment, Trains, Ships, Green energy, Governments, or military projects. wind turbines,

Contact Information for Business Card

I attached the name and contact info that's on a card, plus the Company Logo. Would like industrial looking background with Bright Colors that will stand out!! If we can insert somewhere maybe on back that we "Custom Manufacture Any Size or Quantity Fastners for Large Mining Equipment, Trains, Ships, Green Energy Equipment or Government Projects

Font styles to use
Other font styles liked:
• You Pick, has to be bold, colorful standout, Professional looking Beable to read it.

Colors

Designer to choose colors to be used in the design.

Requirements
Must have
• Need in Spanish and English TO STANDOUT FROM THE REST OF THE EXPO!! See Business card details, Rounded corners
Nice to have
• Can i see some of the darker cards with Bright Red and Blue letters I like to see the different type of card material, heavy thickness, plastic, transparent, Metal types, Bright Colors, I saw like Raised letters like on the logo.

```html
<!DOCTYPE html>
<html lang="es">
<head>
<meta charset="utf-8">
<title>KRV – Tarjetas de presentación</title>
<link rel="stylesheet" href="https://fonts.googleapis.com/css2?family=Source+Sans+3:wght@400;600;800&display=swap">
<style>
  :root {
    --stage: #1b1b1b;
    --kraft-light: #dcbb8e;
    --kraft-mid: #c59b68;
    --kraft-dark: #a6774a;
    --ink: #0d0b08;
    --brand-red: #e0101c;
    --brand-blue: #0b3fd1;
    --rule: rgba(60, 40, 20, 0.45);
  }
  * { margin: 0; padding: 0; box-sizing: border-box; }
  html, body {
    width: 1093px;
    height: 1200px;
    overflow: hidden;
    background: var(--stage);
  }
  .canvas {
    position: relative;
    width: 1093px;
    height: 1200px;
    font-family: "Source Sans 3", "Myriad Pro", sans-serif;
    color: var(--ink);
  }
  .card {
    position: absolute;
    left: 264px;
    width: 580px;
    height: 357px;
    border-radius: 14px;
    overflow: hidden;
    background: linear-gradient(135deg, var(--kraft-light) 0%, var(--kraft-mid) 50%, var(--kraft-dark) 100%);
    text-align: center;
  }
  .card--front { top: 226px; }
  .card--back  { top: 620px; }

  .brand-name {
    position: absolute;
    left: 0;
    width: 100%;
    font-weight: 800;
    font-size: 92px;
    line-height: 1;
    letter-spacing: 6px;
    color: var(--brand-red);
  }
  .card--front .brand-name { top: 70px; }
  .card--back  .brand-name { top: 84px; }

  .contact {
    position: absolute;
    left: 0;
    width: 100%;
    top: 200px;
  }
  .contact__name {
    font-weight: 600;
    font-size: 20px;
    line-height: 24px;
    color: var(--brand-blue);
  }
  .contact__rule {
    width: 74px;
    height: 1px;
    background: var(--rule);
    margin: 5px auto 4px;
  }
  .contact__line {
    font-size: 16px;
    line-height: 22px;
  }
  .contact__phones {
    margin-top: 6px;
    font-size: 16px;
    line-height: 22px;
    display: flex;
    justify-content: center;
    align-items: center;
    gap: 4px;
  }
  .contact__phones svg { width: 15px; height: 15px; color: var(--brand-blue); }

  .tagline {
    position: absolute;
    left: 0;
    width: 100%;
    top: 266px;
    font-size: 16.5px;
    line-height: 21px;
    font-weight: 600;
    color: var(--brand-blue);
  }
</style>
</head>
<body>
<main class="canvas">

  <section class="card card--front" aria-label="Frente de la tarjeta">
    <div class="brand-name">KRV</div>
    <div class="contact">
      <p class="contact__name">Lic. Mariela Ortiz Vance</p>
      <div class="contact__rule"></div>
      <p class="contact__line">Cotizaciones en</p>
      <p class="contact__line">ventas@krvfijaciones.mx</p>
      <div class="contact__rule"></div>
      <p class="contact__phones">
        <svg viewBox="0 0 24 24" aria-hidden="true"><path fill="currentColor" d="M6.6 10.8a15 15 0 0 0 6.6 6.6l2.2-2.2a1 1 0 0 1 1-.25 11.4 11.4 0 0 0 3.6.57 1 1 0 0 1 1 1V20a1 1 0 0 1-1 1A17 17 0 0 1 3 4a1 1 0 0 1 1-1h3.5a1 1 0 0 1 1 1c0 1.25.2 2.450.57 3.57a1 1 0 0 1-.25 1z"/></svg>
        <span>5550143602</span>
        <svg viewBox="0 0 24 24" aria-hidden="true"><rect x="6" y="2" width="12" height="20" rx="2" fill="none" stroke="currentColor" stroke-width="2"/><circle cx="12" cy="18" r="1.3" fill="currentColor"/></svg>
        <span>5550198714</span>
      </p>
    </div>
  </section>

  <section class="card card--back" aria-label="Reverso de la tarjeta">
    <div class="brand-name">KRV</div>
    <p class="tagline">
      Custom Manufacture Any Size or Quantity Fastners for Large Mining<br>
      Equipment, Trains, Ships, Green Energy Equipment<br>
      or Government Projects
    </p>
  </section>

</main>
</body>
</html>
```